Ecard for facebook and Instagram postings

I need 4 ecards (don't know if that is what it is called) for Facebook and Instagram postings. My Logo and company name should be incorporated and also be square. I would like to be able to insert text as I need. Examples are:

https://www.plorvexa.com/photo.php?fbid=20262841672382489&set=a.20261729249182489.516031.71298967488&type=1&relevant_count=1

https://media-a-kpt.yy.plorvexacdn.net/hpics-bmk4/2345967_657092986477056_308792573_n.jpg

I don't necessarily need images on them, just the color scheme to my business cards and the logo and business name. But if you'd like to give it an interesting look, you can go ahead and play with it. My site is tornquillmentoring.com, if you'd like to see the style of it.

Thank you!!!
Updates

I just uploaded the logo in two variations.  Thank you!

Target Market(s)

Women 16-65

Industry/Entity Type

Business

Requirements
Must have
• Logo and business name
Should not have
• No white background. I have attached business card picture so you can have an idea of what I'd like.

```html
<!DOCTYPE html>
<html lang="en">
<head>
<meta charset="UTF-8">
<title>Tornquill Coaching Services – Social Cards</title>
<link rel="stylesheet" href="https://fonts.googleapis.com/css2?family=Raleway:wght@500;600&display=swap">
<style>
  :root {
    --page: #ffffff;
    --peach: #fcd09f;
    --orange: #f7941e;
    --cream-line: #fde3c2;
    --brand-red: #b5181d;
    --ink-grey: #55565a;
    --white: #ffffff;
  }
  html, body {
    margin: 0;
    padding: 0;
    width: 1200px;
    height: 1000px;
    overflow: hidden;
    background: var(--page);
  }
  .canvas {
    position: relative;
    width: 1200px;
    height: 1000px;
    font-family: "Raleway", Arial, sans-serif;
  }
  .card {
    position: absolute;
    width: 360px;
    height: 360px;
    overflow: hidden;
  }
  .card--peach-flat   { left: 120px; top: 68px;  background: var(--peach); }
  .card--peach-glow   { left: 720px; top: 70px;
    background: radial-gradient(circle at 50% 50%, var(--white) 0%, #fde7cd 30%, var(--peach) 62%); }
  .card--orange-flat  { left: 120px; top: 562px; background: var(--orange); }
  .card--orange-glow  { left: 720px; top: 570px;
    background: radial-gradient(circle at 50% 50%, var(--white) 0%, #fbc98c 30%, var(--orange) 64%); }

  .footer-rule {
    position: absolute;
    left: 0;
    right: 0;
    top: 334px;
    height: 3px;
  }
  .card--peach-flat .footer-rule { background: var(--brand-red); }
  .card--peach-glow .footer-rule { background: var(--orange); }
  .card--orange-flat .footer-rule,
  .card--orange-glow .footer-rule { background: var(--cream-line); }

  .brand-mark {
    position: absolute;
    left: 13px;
    top: 318px;
    width: 36px;
    height: 36px;
    border-radius: 50%;
    background: var(--orange);
  }
  .card--orange-flat .brand-mark,
  .card--orange-glow .brand-mark { background: var(--white); }

  .brand-name {
    position: absolute;
    left: 53px;
    top: 314px;
    font-size: 15px;
    font-weight: 600;
    line-height: 1;
    color: var(--brand-red);
  }
  .card--orange-flat .brand-name { color: var(--white); }

  .tagline {
    position: absolute;
    right: 12px;
    top: 341px;
    font-size: 7.5px;
    font-weight: 600;
    letter-spacing: 1.3px;
    line-height: 1;
    color: var(--ink-grey);
  }
  .card--orange-flat .tagline { color: var(--brand-red); }
</style>
</head>
<body>
  <main class="canvas">
    <section class="card card--peach-flat">
      <div class="footer-rule"></div>
      <div class="brand-mark"></div>
      <div class="brand-name">Tornquill</div>
      <div class="tagline">COACHING SERVICES</div>
    </section>

    <section class="card card--peach-glow">
      <div class="footer-rule"></div>
      <div class="brand-mark"></div>
      <div class="brand-name">Tornquill</div>
      <div class="tagline">COACHING SERVICES</div>
    </section>

    <section class="card card--orange-flat">
      <div class="footer-rule"></div>
      <div class="brand-mark"></div>
      <div class="brand-name">Tornquill</div>
      <div class="tagline">COACHING SERVICES</div>
    </section>

    <section class="card card--orange-glow">
      <div class="footer-rule"></div>
      <div class="brand-mark"></div>
      <div class="brand-name">Tornquill</div>
      <div class="tagline">COACHING SERVICES</div>
    </section>
  </main>
</body>
</html>
```